Business Card Design

Looking for business card designs for a new business. there will be two cards of the same design (both lots of information below in contact info). We would like the logo diagonally across the card with the information split above and below the logo similar to sketch. happy to look at similar alternatives
Please use same colours as in logo design

Industry/Entity Type

Business

Contact Information for Business Card

Dwight Halloran
mob - 0491 738 204
ph - 02 6148 3920
fax - 02 6148 3975
email - dwight@kestrelbeams.com.au
14 Larkmoor Road, Corrandale NSW 2391

Colin Marchetti
mob - 0438 912 557
ph - 02 6148 3920
fax - 02 6148 3975
email - colin@kestrelbeams.com.au

```html
<!DOCTYPE html>
<html lang="en">
<head>
<meta charset="utf-8">
<title>Kestrel Beams – Business Cards</title>
<link rel="stylesheet" href="https://fonts.googleapis.com/css2?family=Open+Sans:wght@400;600;700&display=swap">
<style>
  :root {
    --teal: #2b8a85;
    --ink: #231f20;
    --paper: #ffffff;
    --backdrop: #e7e3dd;
  }
  * { margin: 0; padding: 0; box-sizing: border-box; }
  html, body { width: 1040px; height: 1200px; overflow: hidden; }
  body {
    background: var(--backdrop);
    font-family: "Open Sans", Arial, sans-serif;
    color: var(--ink);
    position: relative;
  }
  .card {
    position: absolute;
    left: 53px;
    width: 924px;
    height: 528px;
    background: var(--paper);
    box-shadow: 0 4px 14px rgba(0,0,0,0.18);
    overflow: hidden;
  }
  .card--front { top: 60px; }
  .card--back { top: 620px; }

  .name-badge {
    position: absolute;
    left: 21px; top: 23px;
    width: 363px; height: 60px;
  }
  .name-badge svg { position: absolute; inset: 0; }
  .name-badge__text {
    position: absolute; inset: 0;
    display: flex; align-items: center; justify-content: center;
    color: var(--paper);
    font-weight: 700;
    font-size: 29px;
    letter-spacing: 1.5px;
    text-transform: uppercase;
  }

  .direct-contacts {
    position: absolute;
    left: 42px; top: 100px;
    list-style: none;
  }
  .direct-contacts li {
    display: flex; align-items: center;
    font-size: 25px;
    height: 32px;
    margin-bottom: 12px;
  }

  .icon {
    width: 26px; height: 26px;
    flex: none;
    margin-right: 10px;
    border-radius: 5px;
    background: var(--teal);
    display: inline-flex; align-items: center; justify-content: center;
  }
  .icon svg { width: 18px; height: 18px; }

  .wordmark {
    position: absolute;
    display: flex; align-items: center; gap: 18px;
    white-space: nowrap;
    color: var(--teal);
    font-weight: 700;
    font-size: 80px;
    letter-spacing: -1px;
  }
  .card--front .wordmark { left: 458px; top: 276px; transform: translate(-50%, -50%) rotate(-22deg); }
  .card--back .wordmark { left: 458px; top: 240px; transform: translate(-50%, -50%) rotate(-22deg); }
  .wordmark__square {
    width: 50px; height: 50px;
    background: var(--ink);
    flex: none;
  }

  .office-contacts {
    position: absolute;
    left: 590px; top: 378px;
    list-style: none;
    transform: rotate(-20deg);
    transform-origin: left top;
  }
  .office-contacts li {
    display: flex; align-items: flex-start;
    font-size: 22px;
    line-height: 27px;
    margin-bottom: 6px;
  }
  .office-contacts .icon { margin-top: 1px; }
</style>
</head>
<body>

<section class="card card--front" aria-label="Business card front">
  <div class="name-badge">
    <svg viewBox="0 0 363 60" width="363" height="60" aria-hidden="true">
      <polygon points="0,30 14,0 14,60" fill="var(--teal)"/>
      <polygon points="363,30 349,0 349,60" fill="var(--teal)"/>
      <rect x="16" y="0" width="331" height="60" fill="var(--ink)"/>
    </svg>
    <span class="name-badge__text">Dwight Halloran</span>
  </div>

  <ul class="direct-contacts">
    <li>
      <span class="icon"><svg viewBox="0 0 18 18" aria-hidden="true"><rect x="5" y="2" width="8" height="14" rx="1.5" fill="none" stroke="#fff" stroke-width="1.8"/><rect x="7" y="4.5" width="4" height="6" fill="#fff"/></svg></span>
      0491 738 204
    </li>
    <li>
      <span class="icon"><svg viewBox="0 0 18 18" aria-hidden="true"><rect x="2.5" y="4" width="13" height="10" rx="1" fill="none" stroke="#fff" stroke-width="1.8"/><polyline points="2.5,4.5 9,10 15.5,4.5" fill="none" stroke="#fff" stroke-width="1.8"/></svg></span>
      dwight@kestrelbeams.com.au
    </li>
  </ul>

  <div class="wordmark"><span class="wordmark__square"></span>Kestrel Beams</div>

  <ul class="office-contacts">
    <li>
      <span class="icon"><svg viewBox="0 0 18 18" aria-hidden="true"><path d="M5 2.5 L7.5 6 L6 7.5 Q7.5 10.5 10.5 12 L12 10.5 L15.5 13 L14 15.5 Q6 15 2.5 4 Z" fill="#fff"/></svg></span>
      02 6148 3920
    </li>
    <li>
      <span class="icon"><svg viewBox="0 0 18 18" aria-hidden="true"><rect x="5" y="2.5" width="8" height="4" fill="#fff"/><rect x="2.5" y="7" width="13" height="6" rx="1" fill="#fff"/><rect x="5" y="11" width="8" height="4.5" fill="#fff" stroke="var(--teal)" stroke-width="1"/></svg></span>
      02 6148 3975
    </li>
    <li>
      <span class="icon"><svg viewBox="0 0 18 18" aria-hidden="true"><path d="M9 16 C5 11 4 9 4 7 A5 5 0 0 1 14 7 C14 9 13 11 9 16 Z" fill="#fff"/><circle cx="9" cy="7" r="2" fill="var(--teal)"/></svg></span>
      <span>14 Larkmoor Road<br>Corrandale NSW 2391</span>
    </li>
  </ul>
</section>

<section class="card card--back" aria-label="Business card back">
  <div class="wordmark"><span class="wordmark__square"></span>Kestrel Beams</div>
</section>

</body>
</html>
```